Computer Company needs a Business card design

We need a business card design for our business. We assist people to transition to the KVS (Kestrel Vantage Scheme). The Verandal Crown Office-owned kvs™ network is a brand new telecommunications network currently being rolled out across Australia, giving access to a reliable broadband connection. Our niche market will predominantly be domestic customers in the 50+ age bracket. The assistance that we provide is everything from arranging the equipment, arranging the plan and contract term, appointment times, final testing of the network and any tweaks that need to be made. We basically PM the transition from start to finish. The business card design should be minimalist, should communicate loyalty and stability, should be easy to read and clearly explain what we do. We have asked for front and back. However, the back of the card does not have to include much information at all. It could be just a small design, or a repeat of our phone number. Up to you. The attached file only says what is required on the card. It does not specify where to arrange the text, what fonts to use, etc etc. As much as we would like to give you more info, due to our very limited design ability, we are not really able to send you any rough, or otherwise, designs of what we are after. Hopefully the above description is enough for you.

```html
<!DOCTYPE html>
<html lang="en">
<head>
<meta charset="utf-8">
<title>Tidewell Link – Business Card</title>
<link href="https://fonts.googleapis.com/css2?family=Poppins:wght@500;600&family=Open+Sans:wght@400;700&display=swap" rel="stylesheet">
<style>
  :root {
    --brand-blue: #0b84ad;
    --accent-orange: #ee7d11;
    --card-white: #f7f7f7;
    --backdrop: #dcdcdc;
    --ink-white: #ffffff;
  }
  html, body {
    margin: 0;
    padding: 0;
    overflow: hidden;
  }
  body {
    width: 1200px;
    height: 960px;
    background: var(--backdrop);
    position: relative;
  }
  .card {
    position: absolute;
    left: 320px;
    width: 600px;
    height: 342px;
    box-sizing: border-box;
    overflow: hidden;
  }
  .card-front {
    top: 108px;
    background: var(--brand-blue);
    display: flex;
    align-items: center;
    justify-content: center;
  }
  .wordmark {
    font-family: "Poppins", sans-serif;
    font-weight: 600;
    font-size: 54px;
    letter-spacing: -0.5px;
    line-height: 1;
    margin: 0;
    white-space: nowrap;
  }
  .card-front .wordmark {
    color: var(--ink-white);
    margin-top: 12px;
  }
  .card-back {
    top: 493px;
    background: var(--card-white);
  }
  .back-header {
    height: 195px;
    display: flex;
    align-items: center;
    justify-content: center;
  }
  .back-header .wordmark {
    color: var(--brand-blue);
    margin-top: 42px;
  }
  .accent-rule {
    height: 4px;
    background: var(--accent-orange);
  }
  .back-footer {
    height: 143px;
    background: var(--brand-blue);
    position: relative;
    color: var(--ink-white);
  }
  .person {
    position: absolute;
    right: 348px;
    top: 44px;
    text-align: right;
    font-family: "Open Sans", sans-serif;
  }
  .person-name {
    font-weight: 700;
    font-size: 19px;
    letter-spacing: 0.8px;
    margin: 0;
    line-height: 1.15;
  }
  .person-role {
    font-size: 15px;
    margin: 0;
    line-height: 1.3;
  }
  .contact-list {
    position: absolute;
    left: 280px;
    top: 34px;
    margin: 0;
    padding: 0;
    list-style: none;
    font-family: "Open Sans", sans-serif;
    font-size: 14px;
    line-height: 19px;
  }
  .contact-list li {
    display: flex;
    align-items: center;
    gap: 8px;
  }
  .contact-icon {
    width: 12px;
    height: 12px;
    fill: var(--ink-white);
    flex: none;
  }
</style>
</head>
<body>
  <section class="card card-front">
    <p class="wordmark">Tidewell Link</p>
  </section>

  <section class="card card-back">
    <div class="back-header">
      <p class="wordmark">Tidewell Link</p>
    </div>
    <div class="accent-rule"></div>
    <div class="back-footer">
      <div class="person">
        <p class="person-name">LEON HARCOURT</p>
        <p class="person-role">CEO/FOUNDER</p>
      </div>
      <ul class="contact-list">
        <li>
          <svg class="contact-icon" viewBox="0 0 12 12" aria-hidden="true"><path d="M2.4 0.6l2 2.2-1 1.3c.7 1.5 1.9 2.8 3.5 3.6l1.3-1 2.2 2-1.2 1.9C5.6 10.4 1.6 6.4 0.6 1.8z"/></svg>
          <span>0491550283</span>
        </li>
        <li>
          <svg class="contact-icon" viewBox="0 0 12 12" aria-hidden="true"><path d="M0.5 2.5h11v7h-11z M1 3l5 3.6L11 3" fill="none" stroke="#fff" stroke-width="1"/><path d="M0.5 2.5h11L6 6.5z"/></svg>
          <span>leon@tidewelllink.com.au</span>
        </li>
        <li>
          <svg class="contact-icon" viewBox="0 0 12 12" aria-hidden="true"><circle cx="6" cy="6" r="5.5"/><path d="M3 4.5c1 .2 1.5 1 1.2 2s.8 1.5 1.3 2.7M7 1.5c-.4 1 .5 1.6 1.6 1.7s1 1.5 2 1.6" fill="none" stroke="#0b84ad" stroke-width="1"/></svg>
          <span>www.tidewelllink.com.au</span>
        </li>
      </ul>
    </div>
  </section>
</body>
</html>
```